We need a flyer designed for our 4th Annual Harvestlight: A Kinfolk Homecoming for the Heritage Festival that includes the day, time, location, address, and logos. It also needs to include what to expect. The event will be held on Saturday June 14th from 12p-6p at Cedar Commons located at 417 N. Bellmora St., Pensacola, FL 32507. Please see uploaded files for prior flyers for reference when it comes to information to include. Also I've uploaded pictures from our prior festivals that you may incorporate and logos.

```html
<!DOCTYPE html>
<html lang="en">
<head>
<meta charset="utf-8">
<title>Harvestlight Heritage Festival Flyer</title>
<link rel="stylesheet" href="https://fonts.googleapis.com/css2?family=Anton&family=Open+Sans:wght@700;800&display=swap">
<style>
  :root {
    --black: #000000;
    --white: #ffffff;
    --yellow: #fff200;
    --green: #8dc63f;
    --red: #ed1c24;
    --blue: #27aae1;
    --magenta: #ec008c;
    --orange: #f7941d;
    --purple: #662d91;
    --gold: #d8a03a;
    --pill-grey: #bcbcbc;
    --divider: #2c2c2c;
  }
  html, body { margin: 0; padding: 0; overflow: hidden; background: var(--black); }
  .flyer {
    position: relative;
    width: 927px; height: 1200px;
    overflow: hidden;
    background: var(--black);
    font-family: "Open Sans", Arial, sans-serif;
  }
  .burst-backdrop {
    position: absolute; inset: 0 0 300px 0;
    background:
      conic-gradient(from 200deg at 50% 95%,
        var(--blue) 0deg, var(--green) 25deg, var(--yellow) 55deg,
        var(--orange) 85deg, var(--red) 120deg, var(--magenta) 150deg,
        var(--yellow) 185deg, var(--orange) 215deg, var(--yellow) 250deg,
        var(--magenta) 290deg, var(--purple) 320deg, var(--blue) 360deg);
  }
  .crowd-silhouette {
    position: absolute; left: 0; right: 0; top: 740px; height: 200px;
    background: linear-gradient(to bottom, rgba(0,0,0,0) 0%, rgba(0,0,0,0.75) 45%, var(--black) 80%);
  }
  .host-name {
    position: absolute; left: 330px; top: 92px;
    display: flex; align-items: center; gap: 14px;
    color: var(--black); font-weight: 800; font-size: 27px; line-height: 1.05;
    text-transform: uppercase;
  }
  .host-name .mark { width: 56px; height: 56px; border-radius: 50%; background: var(--black); flex: none; }
  .presents {
    position: absolute; left: 520px; top: 168px; width: 256px; text-align: center;
    font-weight: 800; font-size: 25px; color: var(--black);
  }
  .edition {
    position: absolute; left: 520px; top: 212px; width: 230px; text-align: center;
    font-weight: 800; font-size: 38px; color: var(--black); letter-spacing: -0.5px;
  }
  .edition sup { font-size: 20px; }
  .title {
    position: absolute; left: 0; width: 927px; text-align: center;
    font-family: "Anton", Impact, sans-serif; line-height: 1; margin: 0;
  }
  .title span {
    -webkit-text-stroke: 4px var(--white);
    paint-order: stroke fill;
    text-shadow: 7px 6px 0 var(--black);
  }
  .title-top { top: 250px; font-size: 214px; letter-spacing: 2px; }
  .title-bottom { top: 470px; font-size: 200px; letter-spacing: 6px; }
  .c-green { color: var(--green); } .c-red { color: var(--red); }
  .c-yellow { color: var(--yellow); } .c-blue { color: var(--blue); }
  .c-magenta { color: var(--magenta); }
  .tagline {
    position: absolute; left: 155px; top: 694px; width: 623px; height: 44px;
    border-radius: 22px; background: var(--black);
    color: var(--yellow); font-weight: 700; font-size: 23px;
    display: flex; align-items: center; justify-content: center;
  }
  .date-block { position: absolute; left: 160px; top: 884px; width: 330px; text-align: center; }
  .day { color: var(--white); font-weight: 800; font-size: 40px; line-height: 1; }
  .date { color: var(--yellow); font-family: "Anton", Impact, sans-serif; font-size: 86px; line-height: 1; margin-top: 2px; }
  .date sup { font-size: 48px; vertical-align: 30px; }
  .time { color: var(--white); font-weight: 800; font-size: 34px; line-height: 1; margin-top: 6px; }
  .venue {
    position: absolute; left: 555px; top: 930px; width: 303px; height: 90px;
    border-radius: 45px; background: var(--pill-grey);
    display: flex; align-items: center; gap: 10px; padding-left: 20px; box-sizing: border-box;
    color: var(--black);
  }
  .venue svg { flex: none; }
  .venue-name { font-weight: 800; font-size: 24px; line-height: 1.05; }
  .venue-address { font-weight: 700; font-size: 15.5px; line-height: 1.3; }
  .highlights {
    position: absolute; left: 60px; top: 1070px; width: 510px; text-align: center;
    color: var(--gold); font-weight: 700; font-size: 18.5px; line-height: 25px; text-transform: uppercase;
  }
  .divider { position: absolute; left: 594px; top: 1063px; width: 1px; height: 110px; background: var(--divider); }
  .sponsor {
    position: absolute; left: 630px; top: 1100px; width: 238px; height: 56px;
    background: #0f0f0f; display: flex; align-items: center; gap: 10px; padding-left: 12px; box-sizing: border-box;
    color: var(--white); font-weight: 700; font-size: 16px;
  }
  .sponsor .mark { width: 30px; height: 30px; background: var(--gold); flex: none; }
</style>
</head>
<body>
<main class="flyer">
  <div class="burst-backdrop" role="img" aria-label="Abstract backdrop of bright colour rays with paint splatters"></div>
  <div class="crowd-silhouette" role="img" aria-label="Black silhouette of a cheering festival crowd with raised arms"></div>

  <div class="host-name"><span class="mark"></span><span>The Marlow Family<br>Foundation</span></div>
  <div class="presents">PRESENTS</div>
  <div class="edition">4<sup>th</sup> Annual</div>

  <h1 class="title title-top"><span class="c-green">H</span><span class="c-red">A</span><span class="c-yellow">R</span><span class="c-blue">V</span><span class="c-green">E</span><span class="c-magenta">S</span><span class="c-yellow">T</span></h1>
  <div class="title title-bottom"><span class="c-yellow">L</span><span class="c-red">I</span><span class="c-green">G</span><span class="c-magenta">H</span><span class="c-blue">T</span></div>

  <div class="tagline">A Kinfolk Homecoming for the Heritage Festival</div>

  <div class="date-block">
    <div class="day">SATURDAY</div>
    <div class="date">June 14<sup>th</sup></div>
    <div class="time">12PM-6PM</div>
  </div>

  <div class="venue">
    <svg width="30" height="46" viewBox="0 0 30 46" aria-hidden="true">
      <path d="M15 1C7 1 1 7 1 15c0 10 14 30 14 30s14-20 14-30C29 7 23 1 15 1z" fill="#000"/>
      <circle cx="15" cy="15" r="6" fill="#bcbcbc"/>
    </svg>
    <div>
      <div class="venue-name">CEDAR COMMONS</div>
      <div class="venue-address">417 N. Bellmora St.,<br>Pensacola, FL 32507.</div>
    </div>
  </div>

  <div class="highlights">
    Live Performances | Food Vendors |<br>
    Art/African Clothing | Kids Obstacle Course &amp;<br>
    Play Area | Spades &amp; Domino Tables |<br>
    Bring Your Own Chairs or Picnic Blankets
  </div>

  <div class="divider"></div>

  <div class="sponsor"><span class="mark"></span><span>The Marlow Firm, PLLC</span></div>
</main>
</body>
</html>
```